WordPress webdesign with coding for our company BRISK The Answer

BRISK The Answer is a payrolling company such as Montaval Wages (one of our competitor https://www.montaval-wages.ch/fr/). We need to set up our website in both languages (Fr and Eng). Our logo is enclosed.
we would like something simple explaining what is payrolling in Graph and wording, who we are and a contact page. you can also take some example if needed from our mother company BRISK The Horizon (www.briskthehorizon.ch) or our sister company (www.briskyourstride.ch). we would like to keep the color panel of our logo (ref. Black = PANTONE P Process Black C
Pink = PANTONE P Process Magenta C
Grey = PANTONE 430 C) as the driver of the website.

```html
<!DOCTYPE html>
<html lang="en">
<head>
<meta charset="utf-8">
<title>BRISK The Answer</title>
<link href="https://fonts.googleapis.com/css2?family=Figtree:wght@400;500;600;700;800&display=swap" rel="stylesheet">
<style>
:root{
  --pink:#e8318f;
  --ink:#111111;
  --grey:#7b7f8b;
  --light:#f4f4f4;
  --white:#ffffff;
  --text:#222222;
}
*{box-sizing:border-box;margin:0;padding:0}
html,body{width:1200px;height:3118px;overflow:hidden;background:var(--white)}
body{font-family:"Figtree",Arial,sans-serif;color:var(--text);position:relative}
.abs{position:absolute}
.accent{color:var(--pink)}
.btn{position:absolute;background:var(--pink);color:var(--white);font-weight:700;font-size:16px;
  display:flex;align-items:center;justify-content:center;border-radius:0 14px 0 14px;letter-spacing:.2px}

/* header */
.site-header{top:0;left:0;width:1200px;height:98px;background:var(--white);border-bottom:1px solid #ddd;z-index:3}
.brand{left:138px;top:22px;font-size:42px;font-weight:800;color:var(--ink);letter-spacing:1px;line-height:1}
.brand-sub{display:block;font-size:12px;font-weight:700;letter-spacing:10px;margin-top:6px}
.main-nav{left:486px;top:42px;display:flex;gap:37px;font-size:16px;color:#333}
.main-nav .current{color:var(--pink);font-weight:500}
.lang{left:979px;top:29px;width:84px;height:48px;background:var(--pink);color:#fff;font-weight:700;font-size:15px;
  display:flex;align-items:center;justify-content:center;gap:12px;border-radius:0 12px 0 12px}

/* hero */
.hero{top:98px;left:0;width:1200px;height:616px;overflow:hidden}
.hero-photo{position:absolute;inset:0;background:linear-gradient(90deg,#eeedea 0%,#e6e3de 40%,#c9c2b8 62%,#d8d3cc 100%)}
.hero-band{position:absolute;left:0;top:0}
.hero-title{left:138px;top:194px;font-size:46px;font-weight:700;color:var(--ink)}
.hero-text{left:138px;top:257px;width:470px;font-size:19px;line-height:23px;color:#333}
.dots{left:147px;top:452px;display:flex;gap:7px}
.dots span{width:10px;height:10px;border-radius:50%;background:var(--pink)}
.dots span.open{background:transparent;border:1.5px solid var(--pink)}

/* text blocks */
.section-title{font-size:44px;font-weight:700;color:var(--ink);line-height:1}
.body-copy{font-size:14px;line-height:19.5px;color:#222}
.body-copy p+p{margin-top:19px}

/* payrolling visual */
.pay-visual{left:186px;top:758px;width:354px;height:392px}
.pay-photo{position:absolute;left:0;top:18px;width:354px;height:354px;border-radius:50%;
  background:radial-gradient(circle at 45% 40%,#f1f2f4 0%,#d3d7dd 60%,#a9afb8 100%)}
.pay-ring{position:absolute;left:0;top:0}

/* services */
.services{top:1236px;left:0;width:1200px;height:484px;background:var(--light)}
.card{position:absolute;top:195px;width:294px;height:189px;border:1.5px solid var(--pink);border-radius:0 22px 0 22px;text-align:center}
.card h3{margin-top:50px;font-size:23px;font-weight:700;color:var(--pink)}
.card p{margin:14px auto 0;width:240px;font-size:14px;line-height:19px;color:#333}
.card-icon{position:absolute;left:103px;top:-46px;width:88px;height:88px;border-radius:50%;border:1.5px solid var(--pink);background:#fff;
  display:flex;align-items:center;justify-content:center}
.card-plus{position:absolute;left:128px;bottom:-19px;width:38px;height:38px;border-radius:50%;border:1.5px solid var(--pink);background:var(--light);
  color:var(--pink);font-size:22px;display:flex;align-items:center;justify-content:center;font-weight:300}

/* contact */
.contact{top:2203px;left:0;width:1200px;height:638px;overflow:hidden}
.contact-photo{position:absolute;inset:0;background:linear-gradient(90deg,#c9cbc3 0%,#a9ad9f 30%,#d4d6d0 60%,#cdd0cb 100%)}
.contact-card{left:609px;top:53px;width:453px;height:541px;background:#fff;border-radius:18px}
.field{position:absolute;left:33px;width:387px;border-bottom:1.5px solid var(--pink);font-size:15px;color:#222;padding:0 0 8px 3px}

/* footer */
.site-footer{top:2841px;left:0;width:1200px;height:277px;background:var(--grey);color:#fff;text-align:center}
.footer-brand{position:absolute;left:0;width:1200px;top:46px;font-size:42px;font-weight:800;letter-spacing:1px;line-height:1}
.footer-nav{position:absolute;left:0;width:1200px;top:123px;display:flex;justify-content:center;gap:38px;font-size:15px}
.socials{position:absolute;left:0;width:1200px;top:171px;display:flex;justify-content:center;gap:12px}
.socials span{width:30px;height:30px;border-radius:50%;background:#111}
.socials span.on{background:var(--pink)}
.copyright{position:absolute;left:0;width:1200px;top:218px;font-size:15px}
</style>
</head>
<body>

<header class="abs site-header">
  <div class="abs brand">BRISK<span class="brand-sub">THE ANSWER</span></div>
  <nav class="abs main-nav">
    <span class="current">Home</span><span>What is payrolling</span><span>Who we are</span><span>Contact</span>
  </nav>
  <div class="abs lang">EN
    <svg width="12" height="8" viewBox="0 0 12 8"><path d="M1 1l5 5 5-5" stroke="#fff" stroke-width="2" fill="none"/></svg>
  </div>
</header>

<section class="abs hero">
  <div class="hero-photo" role="img" aria-label="Smiling businesswoman with a coffee cup working at a laptop in a bright office"></div>
  <svg class="hero-band" width="1200" height="616" viewBox="0 0 1200 616">
    <polygon points="0,592 470,566 1200,520 1200,616 0,616" fill="#fff"/>
    <polygon points="470,566 1200,520 1200,614" fill="#e8318f"/>
  </svg>
  <h1 class="abs hero-title">BRISK <span class="accent">The Answer</span></h1>
  <p class="abs hero-text">Lorem ipsum dolor sit amet, consectetur adipiscing elit, sed do eiusmod tempor incididunt ut labore et dolore magna aliqua.</p>
  <div class="btn" style="left:138px;top:359px;width:214px;height:48px">DISCOVER PAYROLLING</div>
  <div class="abs dots"><span></span><span></span><span class="open"></span><span></span></div>
</section>

<section>
  <div class="abs pay-visual">
    <div class="pay-photo" role="img" aria-label="Circular photo of a laptop, calculator and financial charts on a desk"></div>
    <svg class="pay-ring" width="354" height="392" viewBox="0 0 354 392">
      <circle cx="177" cy="195" r="174" fill="none" stroke="#e8318f" stroke-width="3"/>
    </svg>
  </div>
  <h2 class="abs section-title" style="left:614px;top:786px">What is <span class="accent">Payrolling</span></h2>
  <div class="abs body-copy" style="left:614px;top:862px;width:446px">
    <p>Lorem ipsum dolor sit amet, consectetur adipiscing elit, sed do eiusmod tempor incididunt ut labore et dolore magna aliqua. Quis ipsum suspendisse ultrices gravida. Risus commodo viverra maecenas accumsan lacus vel facilisis.</p>
    <p>Lorem ipsum dolor sit amet, consectetur adipiscing elit, sed do eiusmod tempor incididunt ut labore et dolore magna aliqua. Quis ipsum suspendisse ultrices gravida. Risus commodo viverra maecenas accumsan lacus vel facilisis.</p>
  </div>
  <div class="btn" style="left:614px;top:1057px;width:134px;height:48px">LEARN MORE</div>
</section>

<section class="abs services">
  <h2 class="abs section-title" style="left:0;width:1200px;top:53px;text-align:center">Discover all <span class="accent">Our Services</span></h2>

  <div class="card" style="left:138px">
    <div class="card-icon">
      <svg width="54" height="54" viewBox="0 0 54 54" fill="none" stroke="#111" stroke-width="2">
        <circle cx="20" cy="16" r="8"/>
        <path d="M5 46v-6a12 12 0 0 1 24 0v6"/>
        <rect x="32" y="6" width="14" height="18" rx="2" stroke="#e8318f"/>
        <path d="M36 12h6M36 17h6" stroke="#e8318f"/>
        <circle cx="39" cy="38" r="9"/>
        <path d="M39 33v10M36 36h5a2 2 0 0 1 0 3h-4"/>
      </svg>
    </div>
    <h3>Payrolling</h3>
    <p>Lorem ipsum dolor sit amet, consectetur adipiscing elit, sed do eiusmod tempor incididunt</p><div class="card-plus">+</div>
  </div>

  <div class="card" style="left:453px">
    <div class="card-icon">
      <svg width="54" height="54" viewBox="0 0 54 54" fill="none" stroke="#111" stroke-width="2">
        <rect x="13" y="6" width="28" height="22" rx="2"/>
        <path d="M18 12h18M18 17h18M18 22h12" stroke="#e8318f"/>
        <path d="M8 24h38v24H8z"/>
        <rect x="18" y="33" width="18" height="6" stroke="#e8318f"/>
      </svg>
    </div>
    <h3>Sourcing</h3>
    <p>Lorem ipsum dolor sit amet, consectetur adipiscing elit, sed do eiusmod tempor incididunt</p><div class="card-plus">+</div>
  </div>

  <div class="card" style="left:769px">
    <div class="card-icon">
      <svg width="56" height="56" viewBox="0 0 56 56" fill="none" stroke="#111" stroke-width="2">
        <circle cx="28" cy="28" r="7" stroke="#e8318f"/>
        <path d="M28 21V8M28 35v13M21 28H8M35 28h13M23 23l-9-9M33 33l9 9M33 23l9-9M23 33l-9 9"/>
        <circle cx="28" cy="6" r="3" stroke="#e8318f"/><circle cx="28" cy="50" r="3" stroke="#e8318f"/>
        <circle cx="6" cy="28" r="3" stroke="#e8318f"/><circle cx="50" cy="28" r="3" stroke="#e8318f"/>
        <circle cx="12" cy="12" r="3"/><circle cx="44" cy="44" r="3"/>
        <circle cx="44" cy="12" r="3"/><circle cx="12" cy="44" r="3"/>
      </svg>
    </div>
    <h3>Payroll Outsourcing</h3>
    <p>Lorem ipsum dolor sit amet, consectetur adipiscing elit, sed do eiusmod tempor incididunt</p><div class="card-plus">+</div>
  </div>
</section>

<section>
  <h2 class="abs section-title" style="left:138px;top:1794px">Who <span class="accent">We Are</span></h2>
  <div class="abs body-copy" style="left:138px;top:1858px;width:446px">
    <p>Lorem ipsum dolor sit amet, consectetur adipiscing elit, sed do eiusmod tempor incididunt ut labore et dolore magna aliqua. Quis ipsum suspendisse ultrices gravida. Risus commodo viverra maecenas accumsan lacus vel facilisis.</p>
    <p>Lorem ipsum dolor sit amet, consectetur adipiscing elit, sed do eiusmod tempor incididunt ut labore et dolore magna aliqua. Quis ipsum suspendisse ultrices gravida. Risus commodo viverra maecenas accumsan lacus vel facilisis.</p>
  </div>
  <div class="btn" style="left:138px;top:2054px;width:140px;height:48px">LEARN MORE</div>
  <svg class="abs" style="left:630px;top:1745px" width="440" height="430" viewBox="0 0 440 430">
    <path d="M250 10 A205 205 0 0 0 70 400" stroke="#e8318f" stroke-width="10" fill="none"/>
  </svg>
  <div class="abs" role="img" aria-label="Circular photo of a smiling businesswoman on the phone in a bright office"
       style="left:656px;top:1764px;width:390px;height:390px;border-radius:50%;background:radial-gradient(circle at 50% 40%,#e9e5dc,#a9aca6)"></div>
</section>

<section class="abs contact">
  <div class="contact-photo" role="img" aria-label="Woman with curly hair smiling while typing at a desk"></div>
  <div class="abs contact-card">
    <h2 class="abs section-title" style="left:36px;top:48px">Contact <span class="accent">Us</span></h2>
    <div class="field" style="top:126px">Name</div>
    <div class="field" style="top:191px">Email</div>
    <div class="field" style="top:258px">Phone</div>
    <div class="field" style="top:363px">Message</div>
    <div class="btn" style="left:157px;top:442px;width:140px;height:47px">SUBMIT</div>
  </div>
</section>

<footer class="abs site-footer">
  <div class="footer-brand">BRISK The Answer</div>
  <nav class="footer-nav"><span style="font-weight:700">Home</span><span>What is payrolling</span><span>Who we are</span><span>Contact</span></nav>
  <div class="socials"><span></span><span class="on"></span><span></span></div>
  <div class="copyright">© 2025 | www.brisktheanswer.com</div>
</footer>

</body>
</html>
```